Hi,
We are also sourcing for a logo, if you have ideas please take a look at our other project (if you look at our profile you should be able to see it).
We are looking for a website that will be used to manage mobile devices. The feature set is rather small, users can Wipe, Lock, Locate devices as well as make them Ring or Speak (by sending text to be spoken). We attached some images of what it looks like right now. We are looking for simplicity, uniformity and most importantly, the website should be thought of as primary User Interface, it should flow.
Please see attached to get an idea of what it looks like now. The current design was inspired by making a site that will work and flow well on a variety of displays (from mobile to tablet to desktop).
We want to stay away from radio buttons, check-boxes. This should be engaging and creative, opposite of Corporate. Not busy (ideally we are looking to have fewest possible choices at any given time and at the same time no feature should be more than 3 clicks away (this is a suggestion/approximation... just want to share our understanding of what 'flow' is).
Could be cartoony.
Thanks!
BrisketLoom
Reason: there are a couple of designs that are interesting, in addition to specific feedback I provided, possibly looking for more concepts.
Thank You

```html
<!DOCTYPE html>
<html lang="en">
<head>
<meta charset="utf-8">
<title>BrisketLoom – Lost your phone?</title>
<link href="https://fonts.googleapis.com/css2?family=Open+Sans:wght@300;400;600&family=Varela+Round&display=swap" rel="stylesheet">
<style>
  :root {
    --sky-top: #3fb9ef;
    --hero-blue: #2a98dc;
    --hero-deep: #1f86cf;
    --rule-light: rgba(255,255,255,0.45);
    --nav-active: #5cc6f5;
    --white: #ffffff;
    --paper: #fdfdfd;
    --ink: #3b3b3b;
    --footer-ink: #7a7a7a;
    --footer-rule: #d6d6d6;
    --badge-grey: #8f8f8f;
    --device-silver: #d9dde0;
    --device-dark: #2b2d30;
  }
  * { margin: 0; padding: 0; box-sizing: border-box; }
  html, body { width: 1200px; height: 835px; overflow: hidden; }
  body {
    position: relative;
    font-family: "Open Sans", Arial, sans-serif;
    background: var(--paper);
    color: var(--ink);
  }
  .top-bar {
    position: absolute; left: 0; top: 0; width: 1200px; height: 48px;
    background: var(--sky-top);
  }
  .social-links { position: absolute; left: 883px; top: 10px; display: flex; gap: 8px; }
  .social-dot {
    width: 29px; height: 29px; border-radius: 50%;
    background: var(--white); box-shadow: 0 1px 2px rgba(0,0,0,0.2);
  }
  .search-box {
    position: absolute; left: 979px; top: 11px; width: 136px; height: 26px;
    background: var(--white); border: 1px solid #c9d7e0;
    font-size: 11px; font-style: italic; color: #a9a9a9;
    padding: 5px 8px;
  }
  .search-box svg { position: absolute; right: 7px; top: 7px; }
  .hero {
    position: absolute; left: 0; top: 48px; width: 1200px; height: 542px;
    background: linear-gradient(180deg, var(--hero-blue) 0%, var(--hero-deep) 100%);
  }
  .brand {
    position: absolute; left: 86px; top: 68px;
    font-family: "Varela Round", "Open Sans", sans-serif;
    font-size: 52px; color: var(--white); letter-spacing: -0.5px;
  }
  .main-nav { position: absolute; top: 93px; right: 84px; display: flex; }
  .main-nav a {
    display: block; height: 38px; line-height: 38px; padding: 0 22px;
    color: var(--white); text-decoration: none; font-size: 14px;
  }
  .main-nav a.is-active { background: var(--nav-active); }
  .header-rule {
    position: absolute; left: 84px; top: 164px; width: 1032px; height: 1px;
    background: var(--rule-light);
  }
  .device-showcase {
    position: absolute; left: 88px; top: 180px; width: 366px; height: 500px;
    border-radius: 34px;
    background: linear-gradient(100deg, var(--device-dark) 0%, var(--device-dark) 38%, var(--device-silver) 40%, #f4f5f6 70%, var(--device-silver) 100%);
  }
  .headline {
    position: absolute; left: 527px; top: 240px;
    font-weight: 300; font-size: 60px; color: var(--white); letter-spacing: -0.5px;
  }
  .feature-rule {
    position: absolute; left: 531px; width: 585px; height: 1px; background: var(--rule-light);
  }
  .feature-list {
    position: absolute; left: 531px; top: 364px; width: 585px;
    display: flex; justify-content: space-between; list-style: none;
  }
  .feature-list li {
    font-size: 25px; color: var(--white); display: flex; align-items: center;
  }
  .feature-list li::before {
    content: ""; width: 12px; height: 12px; border-radius: 50%;
    background: var(--white); margin-right: 15px;
  }
  .intro {
    position: absolute; left: 531px; top: 454px; width: 585px;
    font-size: 12.5px; line-height: 22px; color: var(--white); text-align: justify;
  }
  .cta-button {
    position: absolute; left: 533px; top: 545px; width: 299px; height: 62px;
    border-radius: 31px; background: var(--white);
    box-shadow: 0 3px 6px rgba(0,0,0,0.25);
    display: flex; align-items: center; padding-left: 28px;
    font-size: 23px; color: var(--ink); text-decoration: none;
  }
  .cta-button svg { position: absolute; right: 28px; top: 19px; }
  .store-note {
    position: absolute; left: 863px; top: 564px; font-size: 12px; color: var(--white);
  }
  .store-badge {
    position: absolute; left: 891px; top: 598px; width: 124px; height: 42px;
    border-radius: 3px; background: var(--badge-grey);
  }
  .footer-rule {
    position: absolute; left: 84px; top: 752px; width: 1032px; height: 1px;
    background: var(--footer-rule);
  }
  .footer-nav {
    position: absolute; left: 84px; top: 784px; font-size: 12.5px; color: var(--footer-ink);
  }
  .footer-nav a { color: var(--footer-ink); text-decoration: none; }
  .footer-nav .sep { margin: 0 8px; }
  .copyright {
    position: absolute; right: 84px; top: 784px; font-size: 12.5px; color: var(--footer-ink);
  }
  .copyright span { margin-left: 12px; }
</style>
</head>
<body>
  <header class="top-bar">
    <div class="social-links">
      <span class="social-dot"></span>
      <span class="social-dot"></span>
    </div>
    <div class="search-box">Search
      <svg width="11" height="11" viewBox="0 0 11 11"><circle cx="4.5" cy="4.5" r="3.3" fill="none" stroke="#b5b5b5" stroke-width="1.3"/><line x1="7" y1="7" x2="10" y2="10" stroke="#b5b5b5" stroke-width="1.5"/></svg>
    </div>
  </header>

  <section class="hero">
  </section>

  <div class="brand">BrisketLoom</div>
  <nav class="main-nav">
    <a href="#" class="is-active">HOME</a>
    <a href="#">ABOUT</a>
    <a href="#">GET THE APPLICATION</a>
    <a href="#">CONTACT</a>
  </nav>
  <div class="header-rule"></div>

  <div class="device-showcase" role="img" aria-label="Two smartphones, one showing a street map with a location pin, the other a lost-phone screen"></div>

  <h1 class="headline">Lost your phone....?</h1>
  <div class="feature-rule" style="top:337px"></div>
  <ul class="feature-list">
    <li>Lock it</li>
    <li>Ring it</li>
    <li>Wipe it</li>
    <li>Find it</li>
  </ul>
  <div class="feature-rule" style="top:427px"></div>
  <p class="intro">Sed ut perspiciatis unde omnis iste natus error sit voluptatem accusantium doloremque laudantium, totam rem aperiam, eaque ipsa quae ab illo inventore veritatis etquasi.</p>

  <a href="#" class="cta-button">Get the application
    <svg width="24" height="24" viewBox="0 0 24 24"><circle cx="12" cy="12" r="10" fill="none" stroke="#4a4a4a" stroke-width="2.2"/><path d="M10 7.5 L14.5 12 L10 16.5" fill="none" stroke="#4a4a4a" stroke-width="2.6" stroke-linecap="round" stroke-linejoin="round"/></svg>
  </a>
  <p class="store-note">also you can get the app on</p>
  <div class="store-badge"></div>

  <div class="footer-rule"></div>
  <footer>
    <nav class="footer-nav">
      <a href="#">Home</a><span class="sep">|</span><a href="#">About</a><span class="sep">|</span><a href="#">Get the Application</a><span class="sep">|</span><a href="#">Contact</a><span class="sep">|</span><a href="#">Privacy</a><span class="sep">|</span><a href="#">Terms and Conditions</a>
    </nav>
    <p class="copyright">Copyright © 2012 www.BrisketLoom.com<span>All rights reserved.</span></p>
  </footer>
</body>
</html>
```